New Company Business Card design

Looking for a corporate looking business card utilising my new logo design - the logo i would like embossed as one option and flat as another - simplistic but stylish - less is more - we are an import export business launching into the market - i would like a couple of options as main background - Grey or Black

```html
<!DOCTYPE html>
<html lang="en">
<head>
<meta charset="utf-8">
<title>Meridian Trade Partners – Business Card</title>
<link href="https://fonts.googleapis.com/css2?family=Cinzel:wght@600&family=Roboto:wght@400;500&display=swap" rel="stylesheet">
<style>
  :root {
    --brand-blue: #2a78bf;
    --brand-grey: #606266;
    --card-white: #f7f7f5;
    --page-bg: #e9e6e1;
    --ink-white: #ffffff;
  }
  * { margin: 0; padding: 0; box-sizing: border-box; }
  html, body { width: 1200px; height: 848px; overflow: hidden; background: var(--page-bg); }
  .canvas { position: relative; width: 1200px; height: 848px; }
  .card {
    position: absolute; left: 280px; width: 640px; height: 366px;
    background: var(--card-white); overflow: hidden;
    box-shadow: 0 2px 6px rgba(0,0,0,0.12);
  }
  .card--front { top: 40px; }
  .card--back { top: 442px; }

  /* Front */
  .front-lockup {
    position: absolute; inset: 0;
    display: flex; flex-direction: column; align-items: center; justify-content: center;
  }
  .wordmark {
    display: flex; align-items: center; gap: 14px;
    font-family: "Cinzel", serif; font-weight: 600; color: var(--brand-blue);
  }
  .wordmark__dot { width: 22px; height: 22px; border-radius: 50%; background: var(--brand-blue); flex: none; }
  .wordmark--front { font-size: 34px; letter-spacing: 1px; }
  .front-rule { width: 330px; height: 2px; background: var(--brand-grey); margin: 12px 0 8px; }
  .tagline {
    font-family: "Cinzel", serif; font-weight: 600; font-size: 13px;
    letter-spacing: 2px; color: var(--brand-grey); text-transform: uppercase;
  }

  /* Back */
  .back-band { position: absolute; inset: 0; width: 640px; height: 366px; }
  .contact {
    position: absolute; left: 44px; top: 118px;
    font-family: "Roboto", sans-serif; color: var(--ink-white);
  }
  .contact__name { font-size: 17px; font-weight: 500; letter-spacing: 0.5px; }
  .contact__role { font-size: 13px; margin-top: 2px; }
  .contact__address { font-size: 13px; line-height: 1.35; margin-top: 12px; }
  .contact__list { list-style: none; margin-top: 10px; font-size: 13px; }
  .contact__list li { display: flex; align-items: center; gap: 10px; line-height: 1.5; }
  .contact__icon { width: 11px; height: 11px; fill: var(--ink-white); flex: none; }
  .wordmark--back {
    position: absolute; left: 460px; right: 30px; top: 130px;
    font-size: 26px; line-height: 1.2; letter-spacing: 0.5px;
    flex-direction: column; align-items: center; gap: 12px; text-align: center;
  }
  .wordmark--back .wordmark__dot { width: 40px; height: 40px; }
</style>
</head>
<body>
<main class="canvas">

  <section class="card card--front" aria-label="Business card front">
    <div class="front-lockup">
      <div class="wordmark wordmark--front">
        <span class="wordmark__dot"></span>
        <span>Meridian Trade Partners</span>
      </div>
      <div class="front-rule"></div>
      <p class="tagline">Worldwide supply for every market</p>
    </div>
  </section>

  <section class="card card--back" aria-label="Business card back">
    <svg class="back-band" viewBox="0 0 640 366" aria-hidden="true">
      <path d="M0 0 L340 0 Q290 200 420 366 L0 366 Z" fill="var(--brand-blue)"/>
    </svg>

    <div class="contact">
      <p class="contact__name">DANIEL HART</p>
      <p class="contact__role">CEO/FOUNDER</p>
      <p class="contact__address">1420 Harbor View Road<br>Juneau, Alaska 99801</p>
      <ul class="contact__list">
        <li><svg class="contact__icon" viewBox="0 0 12 12"><path d="M2 1h3l1 3-1.5 1a6 6 0 0 0 2.5 2.5L8 6l3 1v3c0 .6-.4 1-1 1A9 9 0 0 1 1 2c0-.6.4-1 1-1z"/></svg>555 214 3870</li>
        <li><svg class="contact__icon" viewBox="0 0 12 12"><path d="M3 0h6a1 1 0 0 1 1 1v10a1 1 0 0 1-1 1H3a1 1 0 0 1-1-1V1a1 1 0 0 1 1-1zm0 2v7h6V2z"/></svg>555 907 1642</li>
        <li><svg class="contact__icon" viewBox="0 0 12 12"><path d="M3 0h6v3H3zM1 4h10v5H9v3H3V9H1zm3 4v3h4V8z"/></svg>555 338 5021</li>
        <li><svg class="contact__icon" viewBox="0 0 12 12"><path d="M0 2h12v8H0zm1 1v.3l5 3.2 5-3.2V3z"/></svg>d.hart@meridiantp.com</li>
        <li><svg class="contact__icon" viewBox="0 0 12 12"><circle cx="6" cy="6" r="6"/></svg>www.meridiantp.com</li>
      </ul>
    </div>

    <div class="wordmark wordmark--back">
      <span class="wordmark__dot"></span>
      <span>Meridian<br>Trade<br>Partners</span>
    </div>
  </section>

</main>
</body>
</html>
```